Website for new child psychology practice

New clinical psychology practice in NSW Australia, specialising in work with children, adolescents and families. I would like to feature the colours in the logo, which was recently designed by pixelharbor designer Odette.
I am seeking a professional looking page, which is easy to navigate and is colourful and playful but not childish.
Target Market(s)
Parents and professionals
Industry/Entity Type
Health
Coding
Coded - Design and coding required
Number of Pages Required
1 page
Font styles to use
Serif
Requirements
Must have
- Pages for 'About us' 'Services' 'Fees and information' 'Contact us'
Should not have
- Childish stock photos

```html
<!DOCTYPE html>
<html lang="en">
<head>
<meta charset="utf-8">
<title>Dr Clara Hensley – Clinical Psychologist</title>
<link rel="stylesheet" href="https://fonts.googleapis.com/css2?family=Cinzel:wght@400;600;700&family=Lato:wght@400;700&display=swap">
<style>
:root{
  --purple:#a3288f;
  --purple-deep:#8e1f7d;
  --gold:#d5a55a;
  --gold-light:#f3e9dc;
  --ink:#111111;
  --text:#444444;
  --muted:#6d6d6d;
  --band:#f3f3f3;
  --field:#f2f2f2;
  --white:#ffffff;
  --black:#000000;
}
*{box-sizing:border-box;margin:0;padding:0}
html,body{width:1200px;height:3529px;overflow:hidden}
body{position:relative;background:var(--white);font-family:'Lato',sans-serif;color:var(--text)}
.abs{position:absolute}

/* header */
.topbar{left:0;top:0;width:1200px;height:94px;background:var(--white)}
.pin{left:110px;top:30px;width:36px;height:36px;border-radius:50%;background:var(--purple);display:flex;align-items:center;justify-content:center}
.addr{left:161px;top:25px;font-size:14px;line-height:19px;color:var(--ink)}
.brand{left:0;width:1200px;top:30px;text-align:center;font-family:'Cinzel',serif;font-size:26px;font-weight:600;color:var(--ink);display:flex;justify-content:center;align-items:center;gap:10px}
.brand .dot{width:22px;height:22px;border-radius:50%;background:var(--purple)}
.call-icon{left:869px;top:32px;width:36px;height:36px;border-radius:50%;background:var(--gold);display:flex;align-items:center;justify-content:center}
.call{left:914px;top:28px;font-family:'Cinzel',serif;color:var(--ink)}
.call small{display:block;font-size:14px;font-weight:700}
.call b{font-size:18px;font-weight:700}

/* hero */
.hero{left:0;top:94px;width:1200px;height:647px;background:linear-gradient(100deg,#d9d3cf 0%,#ecebeb 45%,#f4f4f4 60%,#dfe3ea 100%)}
.nav{left:318px;top:132px;display:flex;gap:48px;font-size:15px;color:var(--ink)}
.hero-panel{left:0;top:243px;width:632px;height:365px;background:rgba(160,30,140,.9)}
.hero-title{left:105px;top:290px;width:515px;white-space:nowrap;font-family:'Cinzel',serif;font-weight:700;font-size:44px;line-height:56px;color:var(--white)}
.hero-sub{left:112px;top:352px;font-family:'Cinzel',serif;font-weight:600;font-size:29px;color:var(--gold)}
.hero-text{left:108px;top:403px;width:470px;font-size:15px;line-height:26px;color:var(--white)}
.btn{display:flex;align-items:center;justify-content:center;gap:18px;font-family:'Cinzel',serif;font-weight:700;font-size:15px;color:var(--white);background:var(--gold);border-radius:5px}
.hero-btn{left:110px;top:504px;width:204px;height:55px}

/* about */
.about-photo{left:116px;top:823px;width:452px;height:452px;border-radius:50%;background:radial-gradient(circle at 40% 45%,#9fa59a,#5d6358 70%,#3b3d3a)}
.about-title{left:592px;top:874px;font-family:'Cinzel',serif;font-weight:600;font-size:36px;line-height:48px;color:var(--ink);white-space:nowrap}
.about-text{left:595px;top:983px;width:480px;font-size:15px;line-height:30px;color:var(--muted)}
.about-btn{left:593px;top:1160px;width:185px;height:55px}

/* services */
.sec-title{left:0;width:1200px;text-align:center;font-family:'Cinzel',serif;font-weight:600;color:var(--ink)}
.services-title{top:1403px;font-size:36px}
.svc{top:1488px;width:326px;height:374px;text-align:center;border-radius:10px}
.svc.active{background:var(--white);box-shadow:0 8px 30px rgba(0,0,0,.08)}
.svc .ico{width:72px;height:72px;border-radius:50%;background:var(--gold-light);margin:42px auto 0;display:flex;align-items:center;justify-content:center}
.svc.active .ico{background:var(--purple)}
.svc h3{font-family:'Cinzel',serif;font-weight:600;font-size:21px;line-height:26px;color:var(--ink);margin:28px auto 0;width:270px}
.svc .rule{width:38px;height:3px;background:var(--gold);margin:12px auto 0}
.svc.active .rule{background:var(--purple)}
.svc p{font-size:15px;line-height:26px;margin:18px auto 0;width:290px;color:var(--text)}
.svc .more{display:inline-flex;align-items:center;gap:10px;font-family:'Cinzel',serif;font-weight:700;font-size:15px;color:var(--gold);margin-top:20px}
.svc.active .more{color:var(--purple)}

/* testimonials */
.band{left:0;top:1984px;width:1200px;height:663px;background:var(--band)}
.testi-title{top:2052px;font-size:40px}
.avatar{border-radius:50%;background:linear-gradient(160deg,#b9a393,#6d5a50)}
.t-card{left:267px;top:2183px;width:660px;height:384px;background:var(--white)}
.t-text{left:300px;top:2272px;width:594px;text-align:center;font-size:13px;line-height:26px;color:var(--muted)}
.t-rule{left:318px;top:2445px;width:558px;height:1px;background:#e6e6e6}
.quote{font-family:Georgia,serif;font-size:110px;color:#e4e4e4;line-height:1}
.t-name{left:488px;top:2487px;font-family:'Cinzel',serif;font-weight:700;font-size:17px;color:var(--ink)}
.t-role{left:621px;top:2488px;font-size:15px;color:#9a9a9a}
.stars{left:555px;top:2524px;display:flex;gap:4px}
.arrow{width:30px;height:30px;border-radius:50%;display:flex;align-items:center;justify-content:center}

/* contact */
.dark{left:0;top:2960px;width:1200px;height:569px;background:var(--black)}
.contact-card{left:105px;top:2730px;width:988px;height:338px;background:var(--white);border-radius:14px}
.contact-title{left:105px;width:988px;top:2780px;text-align:center;font-family:'Cinzel',serif;font-weight:700;font-size:40px;color:var(--ink)}
.field{height:50px;background:var(--field);border-radius:4px;font-size:13px;color:#666;display:flex;align-items:center;justify-content:space-between;padding:0 22px 0 24px}
.send{left:846px;top:2930px;width:218px;height:50px;background:var(--purple);border-radius:4px;font-family:'Cinzel',serif;font-weight:700;font-size:16px;color:var(--white);display:flex;align-items:center;justify-content:center}

/* footer */
.f-brand{left:100px;top:3188px;display:flex;align-items:center;gap:9px;font-family:'Cinzel',serif;font-weight:600;font-size:23px;color:var(--white)}
.f-brand .dot{width:22px;height:22px;border-radius:50%;background:var(--purple)}
.socials{left:194px;top:3274px;display:flex;gap:8px}
.socials span{width:29px;height:29px;border-radius:50%;background:var(--white);display:flex;align-items:center;justify-content:center}
.socials span i{width:9px;height:9px;border-radius:50%;background:var(--purple)}
.f-head{font-family:'Cinzel',serif;font-weight:700;font-size:19px;color:var(--white)}
.f-text{font-size:15px;line-height:26px;color:var(--white);text-align:center}
.news-field{left:429px;top:3301px;width:273px;height:44px;border-radius:22px;background:var(--white);display:flex;align-items:center;justify-content:space-between;padding:0 4px 0 22px;font-size:14px;color:#999}
.news-field span{width:36px;height:36px;border-radius:50%;background:var(--gold);display:flex;align-items:center;justify-content:center}
.f-list{list-style:none;text-align:center;font-size:15px;line-height:30px;color:var(--white)}
.f-rule{left:110px;top:3425px;width:980px;height:1px;background:#222}
.copy{left:0;width:1200px;top:3457px;text-align:center;font-size:15px;color:var(--white)}
</style>
</head>
<body>

<!-- header -->
<div class="abs topbar"></div>
<div class="abs pin"><svg width="14" height="18" viewBox="0 0 14 18"><path d="M7 0C3.1 0 0 3 0 6.8 0 11.6 7 18 7 18s7-6.4 7-11.2C14 3 10.9 0 7 0z" fill="#fff"/><circle cx="7" cy="7" r="2.4" fill="#a3288f"/></svg></div>
<div class="abs addr">Dr Clara Hensley<br>108 Lorem ipsum dolor sit amet,<br>consectetur adipiscing elit</div>
<div class="abs brand"><span class="dot"></span>Dr Clara Hensley</div>
<div class="abs call-icon"><svg width="16" height="16" viewBox="0 0 24 24"><path d="M6.6 10.8a15.1 15.1 0 0 0 6.6 6.6l2.2-2.2c.3-.3.7-.4 1-.2 1.1.4 2.3.6 3.6.6.6 0 1 .4 1 1V20c0 .6-.4 1-1 1A17 17 0 0 1 3 4c0-.6.4-1 1-1h3.5c.6 0 1 .4 1 1 0 1.3.2 2.5.6 3.6.1.3 0 .7-.2 1z" fill="#fff"/></svg></div>
<div class="abs call"><small>Call Us</small><b>+1 555 014 2290</b></div>

<!-- hero -->
<section class="abs hero" role="img" aria-label="Photo of a smiling psychologist with a laptop in a bright office"></section>
<nav class="abs nav"><span>Home</span><span>About us</span><span>Services</span><span>Fees and information</span><span>Contact us</span></nav>
<div class="abs hero-panel"></div>
<h1 class="abs hero-title">DR.CLARA HENSLEY</h1>
<div class="abs hero-sub">CLINICAL PSYCHOLOGY</div>
<p class="abs hero-text">Lorem ipsum dolor sit amet, consectetur adipiscing elit, sed do eiusmod tempor incididunt ut labore et dolore magna aliqua. Quis ipsum suspendisse ultrices gravida.</p>
<a class="abs btn hero-btn">GET STARTED <svg width="14" height="14" viewBox="0 0 14 14"><circle cx="7" cy="7" r="7" fill="#fff"/><path d="M5.5 4l3 3-3 3" stroke="#d5a55a" stroke-width="1.8" fill="none"/></svg></a>

<!-- about -->
<div class="abs about-photo" role="img" aria-label="Photo of a therapy session between a psychologist and a client"></div>
<h2 class="abs about-title">ABOUT DR.CLARA HENSLEY<br>CLINICAL PSYCHOLOGY</h2>
<p class="abs about-text">Lorem ipsum dolor sit amet, consectetur adipiscing elit, sed do eiusmod tempor incididunt ut labore et dolore magna aliqua. Quis ipsum suspendisse ultrices gravida. Risus commodo viverra maecenas accumsan lacus vel facilisis. Lorem ipsum dolor sit amet, consectetur adipiscing elit, sed do eiusmod</p>
<a class="abs btn about-btn">LEARN MORE <svg width="14" height="14" viewBox="0 0 14 14"><circle cx="7" cy="7" r="7" fill="#fff"/><path d="M5.5 4l3 3-3 3" stroke="#d5a55a" stroke-width="1.8" fill="none"/></svg></a>

<!-- services -->
<h2 class="abs sec-title services-title">Clinical Psychology Services</h2>
<article class="abs svc" style="left:111px">
  <div class="ico"><svg width="30" height="30" viewBox="0 0 30 30" fill="none" stroke="#d5a55a" stroke-width="1.8"><circle cx="15" cy="12" r="8"/><path d="M9 27v-5M21 27v-5"/></svg></div>
  <h3>LOREM IPSUM</h3><div class="rule"></div>
  <p>Lorem ipsum dolor sit amet, consectetur adipiscing elit, sed do eiusmod tempor incididunt ut labore et dolore magna aliqua.</p>
  <span class="more">LEARN MORE <svg width="13" height="13" viewBox="0 0 14 14"><circle cx="7" cy="7" r="7" fill="currentColor"/><path d="M5.5 4l3 3-3 3" stroke="#fff" stroke-width="1.8" fill="none"/></svg></span>
</article>
<article class="abs svc active" style="left:437px">
  <div class="ico"><svg width="30" height="30" viewBox="0 0 30 30" fill="none" stroke="#fff" stroke-width="1.8"><path d="M3 22h8l4 4 12-10"/><circle cx="16" cy="10" r="6"/></svg></div>
  <h3>LOREM IPSUM DOLOR SIT AMET</h3><div class="rule"></div>
  <p>Lorem ipsum dolor sit amet, consectetur adipiscing elit, sed do eiusmod tempor incididunt ut labore et dolore</p>
  <span class="more">LEARN MORE <svg width="13" height="13" viewBox="0 0 14 14"><circle cx="7" cy="7" r="7" fill="currentColor"/><path d="M5.5 4l3 3-3 3" stroke="#fff" stroke-width="1.8" fill="none"/></svg></span>
</article>
<article class="abs svc" style="left:763px">
  <div class="ico"><svg width="30" height="30" viewBox="0 0 30 30" fill="none" stroke="#a3288f" stroke-width="1.8"><rect x="6" y="6" width="18" height="20"/><path d="M10 11h3M17 11h3M10 16h3M17 16h3M13 26v-5h4v5"/></svg></div>
  <h3>LOREM IPSUM DOLOR SIT AMET</h3><div class="rule"></div>
  <p>Lorem ipsum dolor sit amet, consectetur adipiscing elit, sed do eiusmod tempor incididunt ut labore et dolore magna</p>
  <span class="more">LEARN MORE <svg width="13" height="13" viewBox="0 0 14 14"><circle cx="7" cy="7" r="7" fill="currentColor"/><path d="M5.5 4l3 3-3 3" stroke="#fff" stroke-width="1.8" fill="none"/></svg></span>
</article>

<!-- testimonials -->
<section class="abs band"></section>
<h2 class="abs sec-title testi-title">Client Testimonials</h2>
<div class="abs avatar" style="left:108px;top:2096px;width:50px;height:50px" role="img" aria-label="Client portrait"></div>
<div class="abs avatar" style="left:1040px;top:2098px;width:50px;height:50px" role="img" aria-label="Client portrait"></div>
<div class="abs avatar" style="left:207px;top:2214px;width:50px;height:50px" role="img" aria-label="Client portrait"></div>
<div class="abs avatar" style="left:936px;top:2216px;width:52px;height:52px" role="img" aria-label="Client portrait"></div>
<div class="abs arrow" style="left:203px;top:2288px;background:#e6e6e6"><svg width="8" height="10" viewBox="0 0 8 10"><path d="M6 1L2 5l4 4" stroke="#888" stroke-width="1.6" fill="none"/></svg></div>
<div class="abs arrow" style="left:974px;top:2289px;background:var(--purple)"><svg width="8" height="10" viewBox="0 0 8 10"><path d="M2 1l4 4-4 4" stroke="#fff" stroke-width="1.6" fill="none"/></svg></div>
<div class="abs t-card"></div>
<div class="abs avatar" style="left:553px;top:2136px;width:90px;height:90px;border:3px solid #fff" role="img" aria-label="Portrait of the client giving this testimonial"></div>
<p class="abs t-text">Lorem ipsum dolor sit amet, consectetur adipiscing elit, sed do eiusmod tempor incididunt ut labore et dolore magna aliqua. Quis ipsum suspendisse ultrices gravida. Risus commodo viverra maecenas accumsan lacus vel facilisis. Lorem ipsum dolor sit amet, consectetur adipiscing elit, sed do eiusmod tempor incididunt ut labore et dolore magna aliqua. Quis ipsum suspendisse ultrices gravida. Risus commodo viverra maecenas accumsan lacus vel facilisis.</p>
<div class="abs t-rule"></div>
<div class="abs quote" style="left:398px;top:2458px">“</div>
<div class="abs quote" style="left:742px;top:2448px">”</div>
<div class="abs t-name">MARCUS</div>
<div class="abs t-role">Lorem Ipsum</div>
<div class="abs stars">
  <svg width="16" height="16" viewBox="0 0 24 24"><path d="M12 2l3 6.9 7.5.7-5.7 5 1.7 7.4L12 18l-6.5 4 1.7-7.4-5.7-5 7.5-.7z" fill="#f2a91d"/></svg>
  <svg width="16" height="16" viewBox="0 0 24 24"><path d="M12 2l3 6.9 7.5.7-5.7 5 1.7 7.4L12 18l-6.5 4 1.7-7.4-5.7-5 7.5-.7z" fill="#f2a91d"/></svg>
  <svg width="16" height="16" viewBox="0 0 24 24"><path d="M12 2l3 6.9 7.5.7-5.7 5 1.7 7.4L12 18l-6.5 4 1.7-7.4-5.7-5 7.5-.7z" fill="#f2a91d"/></svg>
  <svg width="16" height="16" viewBox="0 0 24 24"><path d="M12 2l3 6.9 7.5.7-5.7 5 1.7 7.4L12 18l-6.5 4 1.7-7.4-5.7-5 7.5-.7z" fill="#f2a91d"/></svg>
  <svg width="16" height="16" viewBox="0 0 24 24"><path d="M12 2l3 6.9 7.5.7-5.7 5 1.7 7.4L12 18l-6.5 4 1.7-7.4-5.7-5 7.5-.7z" fill="#f2a91d"/></svg>
</div>

<!-- contact -->
<section class="abs dark"></section>
<div class="abs contact-card"></div>
<h2 class="abs contact-title">CONTACT US</h2>
<div class="abs field" style="left:130px;top:2862px;width:225px">Full Name <svg width="12" height="12" viewBox="0 0 12 12"><circle cx="6" cy="3.5" r="3" fill="#666"/><path d="M0 12c0-3.5 2.7-5 6-5s6 1.5 6 5z" fill="#666"/></svg></div>
<div class="abs field" style="left:367px;top:2862px;width:225px">Email Address <svg width="13" height="10" viewBox="0 0 13 10"><rect width="13" height="10" rx="1" fill="#666"/><path d="M0 1l6.5 5L13 1" stroke="#f2f2f2" fill="none"/></svg></div>
<div class="abs field" style="left:605px;top:2862px;width:225px">Company</div>
<div class="abs field" style="left:841px;top:2862px;width:225px">Telephone <svg width="12" height="12" viewBox="0 0 12 12"><rect x="1" y="2" width="10" height="10" rx="1" fill="#666"/><rect x="3" y="0" width="6" height="3" fill="#666"/></svg></div>
<div class="abs field" style="left:130px;top:2930px;width:700px">Message</div>
<div class="abs send">SEND MESSAGE</div>

<!-- footer -->
<div class="abs f-brand"><span class="dot"></span>Dr Clara Hensley</div>
<div class="abs socials" aria-label="Social links"><span><i></i></span><span><i></i></span><span><i></i></span></div>
<div class="abs f-head" style="left:420px;top:3180px">SUBSCRIBE TO OUR NEWSLETTER</div>
<p class="abs f-text" style="left:420px;top:3226px;width:330px">Lorem ipsum dolor sit amet, consectetur adipiscing elit, sed do</p>
<div class="abs news-field">Enter Your Email <span><svg width="16" height="16" viewBox="0 0 24 24"><path d="M2 12l20-9-6 19-4-8z" fill="#111"/></svg></span></div>
<div class="abs f-head" style="left:807px;top:3182px">SUPPORT</div>
<ul class="abs f-list" style="left:770px;top:3225px;width:160px"><li>Terms &amp; Conditions</li><li>Privacy Policy</li><li>About Us</li><li>Support</li></ul>
<div class="abs f-head" style="left:975px;top:3182px">QUICK LINK</div>
<ul class="abs f-list" style="left:940px;top:3223px;width:180px;line-height:26px"><li>Home</li><li>About us</li><li>Services</li><li>Fees and information</li><li>Contact usa</li></ul>
<div class="abs f-rule"></div>
<div class="abs copy">©Copyrights 2024 &nbsp;Dr Clara Hensley &nbsp;| &nbsp;&nbsp;All Rights Reserved</div>

</body>
</html>
```